Fun, Clean Business Card For Family Focused Travel Agency

I need a business card using specific colors and fonts as in the uploaded files. Ideally, I would like a large image of the logo on the back and all the contact info on the front. Maybe the stars/dots somewhere in a flowy form.

I do want it the contact information to be clear and easy to read. I don't want it to look too busy. Maybe even a bit minimalist.

I plan or ordering the ROUNDED CORNER business cards from Cardwell Press, so please consider that in your design.

Target Market(s)

Families with children, couples, groups of friends

Contact Information for Business Card

Marla Quint, Owner
Marla@TumbleTrips.example
Cell Phone Number 555-218-4603
Office Phone Number 555-647-1925
Specializing in Glimmerland destinations, Pelican Bay Fun Park, Cruises and All-Inclusive Vacations.

Nice but not required:
www.TumbleTrips.example
Facebook, Instagram, Twitter icons with username: TumbleTrips

Font styles to use
Sans Serif

Requirements
Must have
• Please try to use the colors from the logo as much as possible. I understand lighter shades/colors may be needed for some things.
Should not have
• NO SERIF FONTS. That is really the only thing I do not want at all

```html
<!DOCTYPE html>
<html lang="en">
<head>
<meta charset="utf-8">
<title>Tumble Trips – Business Card</title>
<link rel="stylesheet" href="https://fonts.googleapis.com/css2?family=Exo+2:wght@400;600;700&display=swap">
<style>
  :root {
    --backdrop: #e9eaec;
    --card: #ffffff;
    --navy: #1d2436;
    --teal: #5bbf9f;
    --orange: #e07a2b;
    --ink: #1f2230;
  }
  * { box-sizing: border-box; margin: 0; padding: 0; }
  html, body { width: 1200px; height: 900px; overflow: hidden; }
  body {
    background: var(--backdrop);
    font-family: "Exo 2", Arial, sans-serif;
    color: var(--ink);
    display: flex;
    flex-direction: column;
    align-items: center;
    justify-content: center;
    gap: 44px;
  }
  .card {
    width: 680px;
    height: 388px;
    background: var(--card);
    border-radius: 30px;
    box-shadow: 0 6px 22px rgba(0,0,0,0.16);
    position: relative;
  }
  /* Logo side */
  .card--brand {
    display: flex;
    align-items: center;
    justify-content: center;
  }
  .brand {
    display: flex;
    align-items: center;
    gap: 22px;
  }
  .brand__dot {
    width: 64px; height: 64px;
    border-radius: 50%;
    background: var(--teal);
  }
  .brand__name {
    font-weight: 700;
    font-size: 68px;
    color: var(--navy);
    letter-spacing: 0.5px;
  }
  /* Contact side */
  .card--contact { padding: 0 44px; }
  .contact {
    position: absolute;
    left: 44px;
    bottom: 52px;
    width: 360px;
  }
  .contact__name {
    font-weight: 700;
    font-size: 22px;
    color: var(--teal);
  }
  .contact__role {
    font-size: 18px;
    margin-top: 4px;
  }
  .contact__rules { margin: 10px 0 12px; }
  .contact__rule { height: 2px; width: 100%; }
  .contact__rule--orange { background: var(--orange); margin-bottom: 5px; }
  .contact__rule--teal { background: var(--teal); }
  .contact__list { list-style: none; }
  .contact__item {
    display: flex;
    align-items: center;
    gap: 10px;
    font-size: 20px;
    line-height: 27px;
  }
  .contact__icon { width: 18px; height: 18px; flex: none; }
  .card__mark {
    position: absolute;
    right: 50px;
    top: 70px;
    display: flex;
    flex-direction: column;
    align-items: center;
    gap: 14px;
  }
  .card__mark .brand__dot { width: 110px; height: 110px; }
  .card__mark .brand__name { font-size: 34px; }
</style>
</head>
<body>
  <section class="card card--brand">
    <div class="brand">
      <span class="brand__dot"></span>
      <span class="brand__name">Tumble Trips</span>
    </div>
  </section>

  <section class="card card--contact">
    <div class="card__mark">
      <span class="brand__dot"></span>
      <span class="brand__name">Tumble Trips</span>
    </div>
    <div class="contact">
      <p class="contact__name">Marla Quint</p>
      <p class="contact__role">Owner</p>
      <div class="contact__rules">
        <div class="contact__rule contact__rule--orange"></div>
        <div class="contact__rule contact__rule--teal"></div>
      </div>
      <ul class="contact__list">
        <li class="contact__item">
          <svg class="contact__icon" viewBox="0 0 18 18" aria-hidden="true">
            <circle cx="9" cy="9" r="9" fill="#5bbf9f"/>
            <rect x="4.5" y="6" width="9" height="6.5" fill="#fff"/>
            <path d="M4.5 6 L9 9.6 L13.5 6" fill="none" stroke="#5bbf9f" stroke-width="1"/>
          </svg>
          Marla@TumbleTrips.example
        </li>
        <li class="contact__item">
          <svg class="contact__icon" viewBox="0 0 18 18" aria-hidden="true">
            <circle cx="9" cy="9" r="9" fill="#5bbf9f"/>
            <path d="M6 4.5 L7.8 4.5 L8.4 7 L7.2 7.9 Q8.2 10 10.1 10.8 L11 9.6 L13.5 10.2 L13.5 12 Q13.5 13.4 12 13.4 Q5 12.8 4.6 6 Q4.6 4.5 6 4.5 Z" fill="#fff"/>
          </svg>
          555-218-4603
        </li>
        <li class="contact__item">
          <svg class="contact__icon" viewBox="0 0 18 18" aria-hidden="true">
            <circle cx="9" cy="9" r="9" fill="#5bbf9f"/>
            <path d="M9 4 L14 8.6 L12.6 8.6 L12.6 13.5 L10.2 13.5 L10.2 10.6 L7.8 10.6 L7.8 13.5 L5.4 13.5 L5.4 8.6 L4 8.6 Z" fill="#fff"/>
          </svg>
          555-647-1925
        </li>
      </ul>
    </div>
  </section>
</body>
</html>
```